Business Card Design

Company is a Commercial Building Company specialising in New Construction and existing refurbishments

Industry/Entity Type

Business

Contact Information for Business Card

Liam Porter
Construction Manager
E Liam@marshbuilding.com.au
M 0400 213 594
Mail 14 Tarrant Rise Coralmere WA 6199

```html
<!DOCTYPE html>
<html lang="en">
<head>
<meta charset="utf-8">
<title>Marsh Building &amp; Construction – Business Cards</title>
<link rel="stylesheet" href="https://fonts.googleapis.com/css2?family=Arimo:wght@400;700&display=swap">
<style>
  :root {
    --stage: #e9e6e2;
    --paper: #ffffff;
    --cyan: #10c6e0;
    --slate: #4a5064;
    --slate-deep: #353b4e;
    --ink: #3e4456;
    --text-light: #ffffff;
  }
  html, body {
    margin: 0;
    width: 1200px;
    height: 914px;
    overflow: hidden;
    background: var(--stage);
    font-family: "Arimo", Arial, sans-serif;
  }
  .stage { position: relative; width: 1200px; height: 914px; }

  .card {
    position: absolute;
    width: 540px;
    height: 330px;
    background: var(--paper);
    box-shadow: 0 10px 26px rgba(0,0,0,.22);
    overflow: hidden;
  }
  .card-back { left: 600px; top: 90px; }
  .card-front { left: 60px; top: 480px; }

  /* Wordmark */
  .wordmark { display: flex; align-items: center; gap: 12px; color: var(--ink); font-weight: 700; }
  .wordmark-square { width: 34px; height: 34px; background: var(--ink); flex: none; }
  .wordmark-name { font-size: 21px; line-height: 1.1; letter-spacing: .5px; text-transform: uppercase; }

  /* Back card */
  .card-back .wordmark { position: absolute; left: 0; right: 0; top: 104px; justify-content: center; }
  .back-stripe { position: absolute; left: 0; right: 0; top: 256px; height: 7px; background: var(--cyan); }
  .back-band {
    position: absolute; left: 0; right: 0; top: 270px; bottom: 0;
    background: linear-gradient(90deg, var(--slate), var(--slate-deep));
  }

  /* Front card */
  .front-shapes { position: absolute; inset: 0; }
  .card-front .wordmark { position: absolute; left: 26px; top: 110px; }
  .card-front .wordmark-name { font-size: 18px; }

  .holder { position: absolute; right: 30px; top: 70px; text-align: right; }
  .holder-name { margin: 0; font-size: 36px; font-weight: 400; color: var(--text-light); letter-spacing: .3px; }
  .holder-role { margin: 4px 0 0; font-size: 13px; color: var(--slate-deep); }

  .contacts {
    position: absolute; right: 24px; top: 196px;
    margin: 0; padding: 0; list-style: none;
    color: var(--text-light); font-size: 15px;
  }
  .contacts li { display: flex; align-items: center; justify-content: flex-end; gap: 14px; height: 28px; white-space: nowrap; }
  .contacts svg { width: 14px; height: 14px; fill: var(--cyan); flex: none; }
</style>
</head>
<body>
<main class="stage">

  <section class="card card-back" aria-label="Business card back">
    <div class="wordmark">
      <span class="wordmark-square"></span>
      <span class="wordmark-name">Marsh Building<br>&amp; Construction</span>
    </div>
    <div class="back-stripe"></div>
    <div class="back-band"></div>
  </section>

  <section class="card card-front" aria-label="Business card front">
    <svg class="front-shapes" viewBox="0 0 540 330" width="540" height="330" aria-hidden="true">
      <defs>
        <linearGradient id="slateFade" x1="0" y1="0" x2="1" y2="1">
          <stop offset="0" stop-color="#5a6075"/>
          <stop offset="1" stop-color="#353b4e"/>
        </linearGradient>
      </defs>
      <polygon points="222,0 540,0 540,330 96,330 266,150" fill="url(#slateFade)"/>
      <polygon points="240,0 540,0 540,190 282,148" fill="#10c6e0"/>
    </svg>

    <div class="wordmark">
      <span class="wordmark-square"></span>
      <span class="wordmark-name">Marsh Building<br>&amp; Construction</span>
    </div>

    <div class="holder">
      <h1 class="holder-name">Liam Porter</h1>
      <p class="holder-role">Construction Manager</p>
    </div>

    <ul class="contacts">
      <li>0400 213 594
        <svg viewBox="0 0 24 24" aria-label="Phone"><path d="M6.6 10.8a15 15 0 0 0 6.6 6.6l2.2-2.2a1 1 0 0 1 1-.25 11.4 11.4 0 0 0 3.6.57 1 1 0 0 1 1 1V20a1 1 0 0 1-1 1A17 17 0 0 1 3 4a1 1 0 0 1 1-1h3.5a1 1 0 0 1 1 1c0 1.25.2 2.450.57 3.57a1 1 0 0 1-.25 1z"/></svg>
      </li>
      <li>Liam@marshbuilding.com.au
        <svg viewBox="0 0 24 24" aria-label="Email"><path d="M2 5h20v14H2zm2 2v.5l8 5 8-5V7l-8 5z"/></svg>
      </li>
      <li>14 Tarrant Rise Coralmere WA 6199
        <svg viewBox="0 0 24 24" aria-label="Address"><path d="M12 2a7 7 0 0 0-7 7c0 5.25 7 13 7 13s7-7.75 7-13a7 7 0 0 0-7-7zm0 9.5A2.5 2.5 0 1 1 12 6.5a2.5 2.5 0 0 1 0 5z"/></svg>
      </li>
    </ul>
  </section>

</main>
</body>
</html>
```